Detail Shop Business card design

i need a business card design for my new detailing company called 'Brisk's Polish Works'. i want an all black and white design . simple, direct and to the point. i want the designer to choose a fitting font to match the logothe front should have logo, address, phone and email and the back side should have a slogan and text indicating that we offer services on anything including cars, trucks, motorcycles and RVs. slogan will read "we take pride in your ride"
maybe also very small on the back side the IG icon with Brisks_Polish_Works

phone 208.417.6352
address 3847 E Larkin Ave
Spokane WA 99214
email: BrisksPolish@mailvexo.com

Target Market(s)

all ages , auto enthusiasts

Industry/Entity Type

Automotive

Contact Information for Business Card

the front should have logo, address, phone and email and the back side should have a slogan and text indicating that we offer services on anything including cars, trucks, motorcycles and RVs. slogan will read "we take pride in your ride"

phone 208.417.6352
address 3847 E Larkin Ave
Spokane WA 99214

Colors
000000
ffffff

Requirements
Must have
• bold font and very simple design with good spacing
Nice to have
• anything creative from the designer indicating we service any types of vehicles
Should not have
• any colors ,

```html
<!DOCTYPE html>
<html lang="en">
<head>
<meta charset="utf-8">
<title>Brisk's Polish Works – Business Card</title>
<link href="https://fonts.googleapis.com/css2?family=Roboto+Slab:wght@400;600;700&display=swap" rel="stylesheet">
<style>
  :root {
    --backdrop: #1b1b1c;
    --card: #151515;
    --card-edge: #2a2a2a;
    --ink: #ffffff;
    --ink-soft: #d6d6d6;
    --mark: #bdbdbd;
  }
  * { margin: 0; padding: 0; box-sizing: border-box; }
  html, body {
    width: 1200px; height: 900px; overflow: hidden;
    background: var(--backdrop);
    font-family: "Roboto Slab", Georgia, serif;
    color: var(--ink);
  }
  .canvas {
    width: 1200px; height: 900px;
    display: flex; flex-direction: column; align-items: center;
    justify-content: center; gap: 24px;
  }
  .card {
    position: relative;
    width: 700px; height: 400px;
    background: var(--card);
    border: 1px solid var(--card-edge);
    box-shadow: 0 12px 30px rgba(0,0,0,.55);
  }

  /* Back side */
  .card--back {
    display: flex; flex-direction: column; align-items: center; justify-content: center;
  }
  .brand {
    display: flex; align-items: center; gap: 14px;
    font-weight: 700; color: var(--mark); letter-spacing: .02em;
  }
  .brand__dot {
    border: 3px solid var(--mark); border-radius: 50%;
  }
  .card--back .brand { font-size: 30px; margin-bottom: 46px; }
  .card--back .brand__dot { width: 34px; height: 34px; }
  .slogan {
    display: flex; align-items: center; gap: 14px;
    font-size: 17px; font-weight: 600; letter-spacing: .08em; text-transform: uppercase;
  }
  .slogan__rule { width: 56px; height: 1px; background: var(--ink); }
  .services {
    margin-top: 10px;
    font-size: 17px; font-weight: 600; letter-spacing: .06em; text-transform: uppercase;
  }

  /* Front side */
  .card--front { padding: 54px 0 0 62px; }
  .person__name { font-size: 27px; font-weight: 700; letter-spacing: .04em; text-transform: uppercase; }
  .person__role { font-size: 15px; color: var(--ink-soft); }
  .address { margin-top: 62px; font-size: 18px; line-height: 1.35; }
  .contacts { margin-top: 44px; list-style: none; font-size: 18px; line-height: 1.4; }
  .contacts li { display: flex; align-items: center; gap: 10px; }
  .contacts svg { width: 13px; height: 13px; flex: none; }
  .card--front .brand {
    position: absolute; right: 48px; top: 170px;
    font-size: 26px;
  }
  .card--front .brand__dot { width: 40px; height: 40px; }
</style>
</head>
<body>
<main class="canvas">

  <section class="card card--back" aria-label="Card back">
    <div class="brand"><span class="brand__dot"></span>Brisk's Polish Works</div>
    <p class="slogan"><span class="slogan__rule"></span>We take pride in your ride<span class="slogan__rule"></span></p>
    <p class="services">Cars - Trucks - Motorcycles and RVs</p>
  </section>

  <section class="card card--front" aria-label="Card front">
    <h1 class="person__name">Darren Holt</h1>
    <p class="person__role">Director</p>

    <address class="address" style="font-style:normal">
      3847 E Larkin Ave<br>Spokane WA 99214
    </address>

    <ul class="contacts">
      <li>
        <svg viewBox="0 0 16 16" aria-hidden="true"><path fill="#fff" d="M3.6 1.5l2.3 2.3-1.3 1.8c.9 1.9 2.4 3.4 4.3 4.3l1.8-1.3 2.3 2.3-1.6 2c-5.3-.6-9.2-4.5-9.8-9.8z"/></svg>
        208.417.6352
      </li>
      <li>
        <svg viewBox="0 0 16 16" aria-hidden="true"><rect x="1.5" y="3.5" width="13" height="9" fill="none" stroke="#fff" stroke-width="1.4"/><path d="M1.5 3.5l6.5 5 6.5-5" fill="none" stroke="#fff" stroke-width="1.4"/></svg>
        BrisksPolish@mailvexo.com
      </li>
      <li>
        <svg viewBox="0 0 16 16" aria-hidden="true"><circle cx="8" cy="8" r="6.3" fill="none" stroke="#fff" stroke-width="1.3"/><path d="M1.7 8h12.6M8 1.7c-3 3.4-3 9.2 0 12.6M8 1.7c3 3.4 3 9.2 0 12.6" fill="none" stroke="#fff" stroke-width="1.1"/></svg>
        www.BrisksPolishWorks.com
      </li>
    </ul>

    <div class="brand"><span class="brand__dot"></span>Brisk's Polish Works</div>
  </section>

</main>
</body>
</html>
```